High-end law practice specializing in closely held business succession planning and complex estates

Solo practitioner whose practice specializes in high-net worth, complex estate planning needs muliple versions of letterhead black and white, please. Letterhead should incorporate slogan, "Guarding your family legacy is my life's work," for one and "Complex Estate Planning"; third with no slogan. All for The Law Office of Marcy Lynn Pettibone, PC, 418 Cedar Hollow Ln., Linden Ridge, Virginia 23648, Tel. 757-555-0142 Fax tbd email: marcy@mlplawgroup.example; Marcy Lynn Pettibone, Esq., principal, Licensed in VA, MD, PA
Updates

Project Deadline Extended
Reason: My internet service went down and I can only view designs on my smart phone -- it's just too hard to review. So sorry! Working with my ISP now. Please be patient!

Target Market(s)

High net worth clients with complex estate planning needs, family businesses, family farmers, family foresters -- people with unique estate/succession planning needs who need a specialist who understands them.

Industry/Entity Type

Business

Font styles to use
Script

Requirements
Must have
• A high-end look and feel, connoting trustworthiness, special knowledge, and expertise.

```html
<!DOCTYPE html>
<html lang="en">
<head>
<meta charset="utf-8">
<title>Letterhead – The Law Office of Marcy Lynn Pettibone, PC</title>
<link href="https://fonts.googleapis.com/css2?family=Libre+Caslon+Text:wght@400;700&family=Crimson+Text:wght@400&display=swap" rel="stylesheet">
<style>
  :root {
    --backdrop: #d2d2d2;
    --paper: #f1f1f1;
    --ink: #1f1f1f;
    --ink-soft: #333333;
    --rule: #a8a8a8;
    --watermark: #e6e6e6;
    --band: #2a2a2a;
  }
  html, body {
    margin: 0;
    padding: 0;
    width: 1200px;
    height: 1041px;
    overflow: hidden;
    background: var(--backdrop);
  }
  .letterhead {
    position: absolute;
    left: 280px;
    top: 106px;
    width: 638px;
    height: 826px;
    background: var(--paper);
    overflow: hidden;
    font-family: "Libre Caslon Text", Georgia, serif;
    color: var(--ink);
  }
  .top-arc {
    position: absolute;
    left: 0;
    top: 0;
    width: 638px;
    height: 10px;
  }
  .brand-mark {
    position: absolute;
    top: 54px;
    left: 0;
    width: 100%;
    text-align: center;
    font-size: 22px;
    font-weight: 700;
    line-height: 1;
    letter-spacing: 1.5px;
    color: var(--ink);
  }
  .firm-name {
    position: absolute;
    top: 103px;
    left: 0;
    width: 100%;
    text-align: center;
    margin: 0;
    font-weight: 400;
    line-height: 1;
  }
  .firm-name .title {
    display: block;
    font-size: 18.5px;
    letter-spacing: 0.3px;
  }
  .firm-name .subtitle {
    display: block;
    margin-top: 2px;
    font-size: 11.5px;
  }
  .watermark {
    position: absolute;
    top: 360px;
    left: 0;
    width: 100%;
    text-align: center;
    font-size: 150px;
    font-weight: 700;
    letter-spacing: 6px;
    line-height: 1;
    color: var(--watermark);
    user-select: none;
  }
  .footer {
    position: absolute;
    left: 0;
    width: 100%;
    top: 762px;
    text-align: center;
    font-family: "Crimson Text", Georgia, serif;
    color: var(--ink-soft);
  }
  .slogan {
    margin: 0;
    font-size: 9.5px;
    line-height: 12px;
    letter-spacing: 0.2px;
    color: var(--ink);
  }
  .footer-rule {
    width: 400px;
    height: 0;
    border: 0;
    border-top: 1px solid var(--rule);
    margin: 5px auto 4px;
  }
  .contact {
    margin: 0;
    font-size: 7.5px;
    line-height: 10px;
    white-space: nowrap;
  }
</style>
</head>
<body>
  <div class="letterhead">
    <svg class="top-arc" viewBox="0 0 638 10" aria-hidden="true">
      <path d="M72 0 L568 0 Q320 16 72 0 Z" fill="var(--band)"/>
    </svg>

    <div class="brand-mark">MLP</div>

    <h1 class="firm-name">
      <span class="title">THE LAW OFFICE</span>
      <span class="subtitle">of Marcy Lynn Pettibone, PC</span>
    </h1>

    <div class="watermark" aria-hidden="true">MLP</div>

    <div class="footer">
      <p class="slogan">GUARDING YOUR FAMILY LEGACY IS MY LIFE'S WORK</p>
      <hr class="footer-rule">
      <p class="contact">418 Cedar Hollow Ln., Linden Ridge, Virginia 23648 · T: 757-555-0142 · F: 757-555-0187 · E: marcy@mlplawgroup.example</p>
      <p class="contact">Marcy Lynn Pettibone, Esq. · Principal · Licensed in VA, MD, PA</p>
    </div>
  </div>
</body>
</html>
```